Verlindo Magician

I want the business card for my business to give to people who watch that later I will be employed to show magic here is my website http://www.verlindoillusions.example/I want the interesting design , i am very opened for formal and informal, I watch a lot of design so don't stick to the common shape and form but i hope it can also be produced the thing to write on will be the same as in picture that i will upload , i also will upload the logo for you that so can be easy to useDenis CostilleMagicianMAGICIAN BALSAMO 17 rue des Tilleuls - 25000 BESANÇON contact@verlindoillusions.example tel. 0381 946 157 tel. 0674 219 503

```html
<!DOCTYPE html>
<html lang="fr">
<head>
<meta charset="utf-8">
<title>Verlindo Magician – Business Card</title>
<link rel="stylesheet" href="https://fonts.googleapis.com/css2?family=Open+Sans:wght@400;700&display=swap">
<style>
  :root {
    --backdrop: #d9d9db;
    --card-white: #ffffff;
    --card-black: #0b0b0b;
    --ink: #1a1a1a;
    --art-dark: #111111;
    --art-mid: #3a3a3a;
    --accent-red: #e2312a;
    --text-light: #f2f2f2;
    --radius: 26px;
  }
  * { box-sizing: border-box; margin: 0; padding: 0; }
  html, body {
    width: 1200px; height: 900px; overflow: hidden;
    background: var(--backdrop);
    font-family: "Open Sans", Arial, sans-serif;
  }
  .stage {
    width: 1200px; height: 900px;
    display: flex; flex-direction: column;
    align-items: center; justify-content: center; gap: 40px;
  }
  .card {
    width: 680px; height: 389px;
    border-radius: var(--radius);
    overflow: hidden;
    box-shadow: 0 6px 18px rgba(0,0,0,0.18);
    background: var(--card-white);
    position: relative;
  }

  .brand {
    display: flex; flex-direction: column; align-items: center;
    color: var(--ink);
  }
  .brand__art {
    background: linear-gradient(160deg, var(--art-mid), var(--art-dark) 60%);
    border-radius: 48% 48% 14px 14px / 40% 40% 14px 14px;
  }
  .brand__name {
    font-weight: 400; letter-spacing: 0.08em;
    text-transform: uppercase; text-align: center;
    line-height: 1.05;
  }

  .card--front { display: flex; align-items: center; justify-content: center; }
  .card--front .brand__art { width: 176px; height: 150px; }
  .card--front .brand__name { font-size: 30px; margin-top: 12px; }

  .card--back { display: flex; }
  .back__identity {
    width: 43%; display: flex; align-items: center; justify-content: center;
    padding-top: 10px;
  }
  .card--back .brand__art { width: 200px; height: 172px; }
  .card--back .brand__name { font-size: 30px; margin-top: 12px; }

  .back__details {
    flex: 1; background: var(--card-black); color: var(--text-light);
    padding: 66px 24px 0 34px;
    font-size: 19px; line-height: 1.28;
  }
  .holder__name {
    color: var(--accent-red); font-weight: 700; font-size: 25px;
    text-transform: uppercase; line-height: 1.1;
  }
  .holder__role { margin-bottom: 8px; }
  .contact-list { list-style: none; }
  .contact-list li { display: flex; align-items: center; gap: 9px; white-space: nowrap; }
  .contact-list svg { width: 15px; height: 15px; flex: none; fill: var(--accent-red); }
  .studio__name {
    color: var(--accent-red); font-weight: 700; text-transform: uppercase;
    margin-top: 2px;
  }
  .studio__address { font-style: normal; }
</style>
</head>
<body>
<main class="stage">
  <section class="card card--front" aria-label="Card front">
    <div class="brand">
      <div class="brand__art" role="img" aria-label="Black and white illustration of the magician holding a playing card"></div>
      <p class="brand__name">Verlindo<br>Magician</p>
    </div>
  </section>

  <section class="card card--back" aria-label="Card back">
    <div class="back__identity">
      <div class="brand">
        <div class="brand__art" role="img" aria-label="Black and white illustration of the magician holding a playing card"></div>
        <p class="brand__name">Verlindo<br>Magician</p>
      </div>
    </div>
    <div class="back__details">
      <p class="holder__name">Marc Ravoulet</p>
      <p class="holder__role">Magician</p>
      <ul class="contact-list">
        <li><svg viewBox="0 0 16 16" aria-hidden="true"><path d="M3.6 1.5l2.3 2.4-1.3 1.9c.8 1.8 2.4 3.4 4.2 4.3l1.9-1.3 2.4 2.3-1.4 2.4C6.8 13.3 2.7 9.2 1.2 3z"/></svg>0381 946 157</li>
        <li><svg viewBox="0 0 16 16" aria-hidden="true"><path d="M3.6 1.5l2.3 2.4-1.3 1.9c.8 1.8 2.4 3.4 4.2 4.3l1.9-1.3 2.4 2.3-1.4 2.4C6.8 13.3 2.7 9.2 1.2 3z"/></svg>0674 219 503</li>
        <li><svg viewBox="0 0 16 16" aria-hidden="true"><path d="M1 3h14v10H1zM2.5 4.5v.4L8 8.8l5.5-3.9v-.4z"/></svg>contact@verlindoillusions.example</li>
        <li><svg viewBox="0 0 16 16" aria-hidden="true"><circle cx="8" cy="8" r="7"/></svg>www.verlindoillusions.example</li>
      </ul>
      <p class="studio__name">Magician Verlindo</p>
      <address class="studio__address">17 rue des Tilleuls - 25000<br>BESANÇON</address>
    </div>
  </section>
</main>
</body>
</html>
```